Financial Advisor Resource Firm needs business card design

Need business card design for company in Omaha NE called Meridale Circle. We provide resources to financial advisors....workshop programs, retirement analysis, and insurance planning. I would like to see designs that use grays, greens, black, and white colors. The final design should communicate 'collaboration' and be simple yet attractive to financial planning clients. I will attached our logo and another picture of a puzzle piece coming together. I would like the incorporate the puzzle picture somehow, maybe on the back somehow, with color or just the gray scale....OR, the picture be the front of the card with 'Meridale' definition on it (see upload) and then company logo, employee name, title, address on the back (see ppt uploaded). The following disclosure needs to be included somewhere- Advisory services offered through Stonebrook Assets, LLC.
Updates

I uploaded a svg and ai file of the logo

Target Market(s)

Financial planning clients and financial advisors....so pretty diverse age range of about 40-70.

Industry/Entity Type

Financial Planning

Contact Information for Business Card

Tobias L. Fenwright, MBA
Founder/President
5287 E. Larkin Road
Suite 230
Omaha, NE 68190
Phone- (402) 555-0147
Cell- (402) 555-0183
Fax- (402) 555-0129
email- tobias@meridaleplan.example
web address- www.meridaleplan.example

Colors
1b1b1b
474747
d3d3d3
ffffff
9bcb3c
abd036

Requirements
Must have
• Must include logo provided, must be 2 sided, and must have disclosure...all of these items listed in project description

```html
<!DOCTYPE html>
<html lang="en">
<head>
<meta charset="utf-8">
<title>Meridale Circle – Business Card</title>
<link href="https://fonts.googleapis.com/css2?family=Work+Sans:wght@400;500;600;700&display=swap" rel="stylesheet">
<style>
  :root {
    --ink: #0d0d0d;
    --charcoal: #1b1b1b;
    --slate: #474747;
    --mist: #d3d3d3;
    --paper: #ffffff;
    --lime: #9bcb3c;
    --lime-bright: #abd036;
    --backdrop: #a9a9a9;
  }
  * { box-sizing: border-box; margin: 0; padding: 0; }
  html, body {
    width: 1200px; height: 930px; overflow: hidden;
    background: var(--backdrop);
    font-family: "Work Sans", sans-serif;
  }
  .canvas { position: relative; width: 1200px; height: 930px; }

  .card {
    position: absolute;
    width: 620px; height: 354px;
    border-radius: 26px;
    overflow: hidden;
    box-shadow: 0 10px 24px rgba(0,0,0,0.25);
  }
  .card--back { left: 70px; top: 70px; background: var(--ink); }
  .card--front { left: 510px; top: 500px; background: var(--ink); }

  .wordmark {
    display: flex; align-items: center; gap: 12px;
    font-weight: 600; letter-spacing: 0.04em; white-space: nowrap;
  }
  .wordmark__dot { width: 18px; height: 18px; border-radius: 50%; flex: none; }

  .card--back .wordmark {
    position: absolute; left: 50%; top: 50%;
    transform: translate(-50%, -50%);
    color: var(--paper); font-size: 40px;
  }
  .card--back .wordmark__dot { background: var(--paper); }

  .front-shape { position: absolute; inset: 0; }

  .card--front .wordmark {
    position: absolute; right: 40px; top: 62px;
    color: var(--charcoal); font-size: 32px;
  }
  .card--front .wordmark__dot { background: var(--lime); }

  .contact {
    position: absolute; left: 34px; top: 104px;
    color: var(--paper); font-size: 14px; line-height: 18px;
  }
  .contact__name { color: var(--lime-bright); font-weight: 600; font-size: 15px; }
  .contact__title { margin-bottom: 10px; }
  .contact__address { margin-bottom: 10px; }
  .contact__list { list-style: none; }
  .contact__list li { display: flex; align-items: center; gap: 10px; white-space: nowrap; }
  .contact__icon { width: 11px; height: 11px; flex: none; fill: none; stroke: var(--lime); stroke-width: 1.6; }
  .contact__icon--solid { fill: var(--lime); stroke: none; }
  .contact__web-domain { color: var(--lime-bright); }

  .disclosure {
    position: absolute; left: 34px; bottom: 16px;
    color: var(--mist); font-size: 10px; line-height: 12px;
    letter-spacing: 0.02em; white-space: nowrap;
  }
</style>
</head>
<body>
<main class="canvas">

  <section class="card card--back" aria-label="Card back">
    <div class="wordmark"><span class="wordmark__dot"></span>Meridale Circle</div>
  </section>

  <section class="card card--front" aria-label="Card front">
    <svg class="front-shape" viewBox="0 0 620 354" width="620" height="354" aria-hidden="true">
      <path d="M204,0 C226,150 420,256 620,232 L620,0 Z" fill="var(--lime)"/>
      <path d="M214,0 C236,142 425,246 620,224 L620,0 Z" fill="var(--paper)"/>
    </svg>

    <div class="wordmark"><span class="wordmark__dot"></span>Meridale Circle</div>

    <div class="contact">
      <p class="contact__name">Tobias L. Fenwright, MBA</p>
      <p class="contact__title">Founder/President</p>
      <p class="contact__address">5287 E. Larkin Road<br>Suite 230 Omaha, NE 68190</p>
      <ul class="contact__list">
        <li><svg class="contact__icon contact__icon--solid" viewBox="0 0 12 12"><path d="M2 1h3l1 3-2 1a6 6 0 0 0 3 3l1-2 3 1v3c-6 0-9-3-9-9z"/></svg><span>(402) 555-0147</span></li>
        <li><svg class="contact__icon" viewBox="0 0 12 12"><rect x="3" y="1" width="6" height="10" rx="1"/></svg><span>(402) 555-0183</span></li>
        <li><svg class="contact__icon contact__icon--solid" viewBox="0 0 12 12"><rect x="3" y="1" width="6" height="3"/><rect x="1" y="5" width="10" height="6" rx="1"/></svg><span>(402) 555-0129</span></li>
        <li><svg class="contact__icon" viewBox="0 0 12 12"><rect x="1" y="2.5" width="10" height="7"/><path d="M1 2.5l5 4 5-4"/></svg><span>tobias@meridaleplan.example</span></li>
        <li><svg class="contact__icon" viewBox="0 0 12 12"><circle cx="6" cy="6" r="5"/><path d="M1 6h10M6 1c-3 3-3 7 0 10M6 1c3 3 3 7 0 10"/></svg><span>www.<span class="contact__web-domain">meridaleplan</span>.example</span></li>
      </ul>
    </div>

    <p class="disclosure">Advisory services offered through Stonebrook Assets, LLC</p>
  </section>

</main>
</body>
</html>
```